Business Card for premium dental clinic

We are a premium dental clinic based in Brasov, Romania with more than 15 year on the market, providing quality dental treatment made by a team of more specialized dentists, working with modern equipment as a solution to beautiful and healthy teeth.

Our current logo for the clinic use 2 square with colors black and gold - dr Ternisu - studio, using family fonts Bodoni, Myriad Pro and Segoe Print.
Depending on the printing we used some gold CMYK background or gold foil picture background or a gold gradient.
We want a business card:
- eye catching business card
- distinguished business card
- premium design
- to keep the color scheme of black and gold
- to attract the customers to spent time reading the information
- modern concept

```html
<!DOCTYPE html>
<html lang="en">
<head>
<meta charset="utf-8">
<title>dr Ternisu – Business Card</title>
<link rel="stylesheet" href="https://fonts.googleapis.com/css2?family=Lato:wght@400;700&family=Oswald:wght@300;400&display=swap">
<style>
  :root {
    --backdrop: #e6e2dc;
    --card-white: #ffffff;
    --card-grey: #e8e8e8;
    --ink-black: #1a191d;
    --gold: #b8892b;
    --gold-light: #c99a35;
    --text-light: #d6d6d6;
    --text-muted: #b5b5b5;
    --text-dark: #111111;
    --rule: #8a8a8a;
  }
  * { margin: 0; padding: 0; box-sizing: border-box; }
  html, body {
    width: 1200px; height: 900px; overflow: hidden;
    background: var(--backdrop);
    font-family: "Lato", sans-serif;
  }
  .canvas { position: relative; width: 1200px; height: 900px; }

  .card {
    position: absolute;
    box-shadow: 3px 4px 6px rgba(0,0,0,0.35);
    overflow: hidden;
  }
  .card-front { left: 329px; top: 90px; width: 556px; height: 345px; background: var(--card-white); }
  .card-back  { left: 329px; top: 469px; width: 560px; height: 344px; background: var(--card-grey); }

  .front-decoration {
    position: absolute; left: 0; top: 150px; width: 556px; height: 56px;
    background: linear-gradient(180deg, var(--card-white) 0%, var(--gold) 55%, var(--ink-black) 100%);
  }
  .front-panel {
    position: absolute; left: 0; top: 206px; width: 556px; height: 139px;
    background: var(--ink-black);
  }

  .brand { position: absolute; left: 35px; top: 72px; }
  .brand-name {
    font-family: "Lato", sans-serif; font-weight: 700;
    font-size: 28px; color: var(--ink-black); letter-spacing: 0.2px;
  }

  .contact {
    position: absolute; right: 28px; top: 213px;
    text-align: right; color: var(--text-light);
    font-size: 15.5px; line-height: 20px;
  }
  .contact-row { display: flex; justify-content: flex-end; align-items: center; gap: 3px; }
  .contact-icon { width: 12px; height: 12px; fill: var(--gold-light); }
  .contact-address { margin-top: 8px; color: var(--text-muted); }

  .person { position: absolute; left: 24px; top: 276px; }
  .person-name {
    font-weight: 700; font-size: 19.5px; color: var(--gold-light);
    letter-spacing: 0.5px;
  }
  .person-title { font-size: 16px; color: var(--text-light); margin-top: -1px; }

  .appointment-title {
    position: absolute; left: 0; right: 0; top: 66px;
    text-align: center; font-family: "Oswald", sans-serif; font-weight: 300;
    font-size: 33px; color: var(--text-dark); letter-spacing: -0.2px;
  }
  .field { position: absolute; left: 79px; width: 393px; }
  .field-label { font-size: 19px; color: var(--text-dark); letter-spacing: 0.5px; }
  .field-rule { position: absolute; left: 8px; right: 0; top: 24px; border-top: 1px solid var(--rule); }
  .field-name { top: 150px; }
  .field-time { top: 206px; }
  .appointment-note {
    position: absolute; left: 0; right: 0; top: 277px;
    text-align: center; font-size: 16.5px; color: var(--text-dark);
  }
</style>
</head>
<body>
<main class="canvas">

  <section class="card card-front" aria-label="Business card front">
    <div class="front-decoration" role="img" aria-label="Gold and black wave decoration"></div>
    <div class="front-panel"></div>

    <div class="brand">
      <span class="brand-name">dr Ternisu</span>
    </div>

    <div class="contact">
      <div class="contact-row">044-555 018 240
        <svg class="contact-icon" viewBox="0 0 12 12"><path d="M1,5 C1,2 11,2 11,5 L9,6 L8,4 L4,4 L3,6 Z M3,7 L9,7 L10,11 L2,11 Z"/></svg>
      </div>
      <div class="contact-row">hello@ternisu.ro
        <svg class="contact-icon" viewBox="0 0 12 12"><path d="M0,2 H12 V10 H0 Z M0.5,2.5 L6,7 L11.5,2.5" stroke="var(--ink-black)" stroke-width="0.8"/></svg>
      </div>
      <div class="contact-row">www.ternisuclinic.ro
        <svg class="contact-icon" viewBox="0 0 12 12"><circle cx="6" cy="6" r="5.5"/></svg>
      </div>
      <div class="contact-address">118, Livezii Street<br>Brasov, 500032, Romania</div>
    </div>

    <div class="person">
      <div class="person-name">MARCUS ELLERY</div>
      <div class="person-title">Managing Director</div>
    </div>
  </section>

  <section class="card card-back" aria-label="Business card back">
    <h1 class="appointment-title">YOUR NEXT APPOINTMENT</h1>
    <div class="field field-name"><span class="field-label">NAME</span><span class="field-rule"></span></div>
    <div class="field field-time"><span class="field-label">TIME</span><span class="field-rule"></span></div>
    <p class="appointment-note">If unable to keep appointment, kindly give 24hrs notice.</p>
  </section>

</main>
</body>
</html>
```